Business Card for beauty technology startup

Design Glimora Business Card for a Beauty, based on the website identity and colors (https://www.glimora-example.com).
Glimora is a beauty tech startup that gathers helpful product info for beauty lovers and consumers (such as availability on stores, price range and product reviews) for makeup products. The card design must be young, colorful but clean, and very modern.

Target Market(s)

woman, 15-35

Industry/Entity Type

Cosmetics

Contact Information for Business Card

Full Name, address, phone

Font styles to use
Other font styles liked:
• Advent Pro

Colors
e34297
86cfc6
ffffff
5c5c5c
e8e8e8
e667a6
b2b2b2

Requirements
Must have
• One full colored side with a creative design and another with card info
• Use Color palette: #95C5C5 and/or #D38AA5
• Use fonts: Advent Pro
• Use website identity: https://www.glimora-example.com
Nice to have
• If needed extra font: Roboto

```html
<!DOCTYPE html>
<html lang="en">
<head>
<meta charset="UTF-8">
<title>Glimora Business Card</title>
<link href="https://fonts.googleapis.com/css2?family=Advent+Pro:wght@300;400&family=Roboto:wght@400;500&display=swap" rel="stylesheet">
<style>
  :root {
    --backdrop: #d6d6d6;
    --card-white: #f7f7f7;
    --rose: #b97a8f;
    --rose-soft: #c08a9c;
    --slate: #5c5c5c;
    --band-grey: #7a7b7d;
    --card-dark: #1a1a1c;
    --ring-dark: #2a2628;
    --url-grey: #4a4a4c;
    --ink-white: #ffffff;
  }
  * { margin: 0; padding: 0; box-sizing: border-box; }
  html, body { width: 1200px; height: 960px; overflow: hidden; }
  body { background: var(--backdrop); position: relative; font-family: "Roboto", sans-serif; }

  .card {
    position: absolute;
    width: 600px;
    height: 342px;
    border-radius: 18px;
    overflow: hidden;
  }
  .card-front { left: 314px; top: 113px; background: var(--card-white); }
  .card-back { left: 311px; top: 472px; background: var(--card-dark); }

  .front-shapes { position: absolute; inset: 0; }

  .brand-lockup {
    position: absolute;
    left: 20px;
    top: 128px;
    display: flex;
    align-items: center;
    gap: 18px;
  }
  .brand-dot {
    width: 52px; height: 52px;
    border-radius: 50%;
    border: 2px solid var(--rose);
  }
  .brand-name {
    font-family: "Advent Pro", sans-serif;
    font-weight: 300;
    font-size: 46px;
    letter-spacing: 4px;
    color: var(--rose);
    text-transform: uppercase;
    line-height: 1;
  }

  .person {
    position: absolute;
    left: 111px;
    top: 202px;
    display: flex;
    align-items: center;
    white-space: nowrap;
  }
  .person-name {
    font-weight: 500;
    font-size: 19px;
    color: var(--rose);
    padding-right: 8px;
    border-right: 1px solid #b2b2b2;
  }
  .person-title {
    font-weight: 500;
    font-size: 14px;
    color: var(--slate);
    padding-left: 6px;
  }

  .contact {
    position: absolute;
    right: 22px;
    top: 32px;
    text-align: right;
    color: var(--ink-white);
    font-size: 13.5px;
    line-height: 19px;
    white-space: nowrap;
  }
  .contact-address { margin-bottom: 6px; padding-right: 4px; }
  .contact-line {
    display: flex;
    justify-content: flex-end;
    align-items: center;
    gap: 9px;
  }
  .contact-line svg { width: 13px; height: 13px; fill: var(--ink-white); flex: none; }

  .back-ring {
    position: absolute;
    left: 10px;
    top: 28px;
    width: 300px;
    height: 300px;
    border-radius: 50%;
    border: 3px solid var(--ring-dark);
  }
  .back-brand {
    position: absolute;
    right: 32px;
    top: 244px;
    text-align: right;
  }
  .back-brand .brand-name { font-size: 52px; letter-spacing: 5px; color: var(--rose-soft); }
  .back-url {
    margin-top: 6px;
    font-size: 13px;
    letter-spacing: 3px;
    color: var(--url-grey);
  }
</style>
</head>
<body>

<section class="card card-front">
  <svg class="front-shapes" viewBox="0 0 600 342" width="600" height="342">
    <path d="M328,0 C316,140 396,282 530,342 L546,342 C416,280 352,130 370,0 Z" fill="var(--band-grey)"/>
    <path d="M370,0 C352,130 416,280 546,342 L600,342 L600,0 Z" fill="var(--rose)" stroke="var(--ink-white)" stroke-width="3"/>
  </svg>

  <div class="brand-lockup">
    <span class="brand-dot"></span>
    <span class="brand-name">Glimora</span>
  </div>

  <div class="person">
    <span class="person-name">CLARA VANCE</span>
    <span class="person-title">CEO/FOUNDER</span>
  </div>

  <div class="contact">
    <p class="contact-address">4120 Willowbend Road<br>Fairview, Oregon 97024</p>
    <p class="contact-line">555 210 4871
      <svg viewBox="0 0 16 16"><path d="M3.5 1 L6 1 L7 5 L5.3 6.3 C6.2 8.2 7.8 9.8 9.7 10.7 L11 9 L15 10 L15 12.5 C15 13.9 13.9 15 12.5 15 C6.7 15 1 9.3 1 3.5 C1 2.1 2.1 1 3.5 1 Z"/></svg>
    </p>
    <p class="contact-line">555 382 6190
      <svg viewBox="0 0 16 16"><path d="M4 0 H12 A1 1 0 0 1 13 1 V15 A1 1 0 0 1 12 16 H4 A1 1 0 0 1 3 15 V1 A1 1 0 0 1 4 0 Z M5 2 V12 H11 V2 Z"/></svg>
    </p>
    <p class="contact-line">555 764 3025
      <svg viewBox="0 0 16 16"><path d="M4 1 H12 V5 H4 Z M1 6 H15 V12 H12 V15 H4 V12 H1 Z M5 10 V13.5 H11 V10 Z"/></svg>
    </p>
    <p class="contact-line">info@glimora-example.com
      <svg viewBox="0 0 16 16"><path d="M1 3 H15 L8 8.5 Z M1 4.5 L8 10 L15 4.5 V13 H1 Z"/></svg>
    </p>
  </div>
</section>

<section class="card card-back">
  <div class="back-ring"></div>
  <div class="back-brand">
    <div class="brand-name">Glimora</div>
    <div class="back-url">www.glimora-example.com</div>
  </div>
</section>

</body>
</html>
```